Refresh of far from plain IT company website

Our web site is starting to show it's age. You can see the existing site here: www.plumbwick.net. As a growing company we want to come across as a dynamic collection of IT experts.

We want to update the design so are open to any colour palette and look, but want to retain our current table logo. We use the logo on our business cards but with a white background - see the attached file, so you don't need to keep the brown or the green.

The design should consider the range of browsers that will be looking at the site - so please show how it will look on a wide screen laptop and a 768x1024 tablet.

We want to add some pages about our team and their skills, probably with photos of each person on the team.

This is an uncoded project - the PSD files of the design is required, not coding.
Updates

Thanks everyone for the submissions so far.  It's a holiday day in the UK today but we will get some feedback on the designs so far out to you.

Target Market(s)

Architects and other creative types looking for IT support

Industry/Entity Type

Business

Font styles to use
Serif
Sans Serif

Requirements
Must have
• Must look good on a laptop and an iPad.

```html
<!DOCTYPE html>
<html lang="en">
<head>
<meta charset="utf-8">
<title>plumbwick – IT support for business</title>
<link href="https://fonts.googleapis.com/css2?family=Ubuntu:ital,wght@0,400;0,500;0,700;1,700&family=Roboto:wght@400;500&display=swap" rel="stylesheet">
<style>
:root{
  --plum:#8e0f50;
  --gold:#e1b000;
  --ink:#333;
  --rule:#dcdcdc;
  --panel:#efefef;
  --footer:#333333;
  --footer-text:#ffffff;
}
*{box-sizing:border-box;margin:0;padding:0}
html,body{width:1034px;height:1200px;overflow:hidden;background:#fff}
body{position:relative;font-family:'Roboto',sans-serif;color:var(--ink)}
.abs{position:absolute}
.top-rule{left:0;top:0;width:1034px;height:3px;background:var(--plum)}
.brand{left:198px;top:26px;display:flex;align-items:center;gap:14px}
.brand-mark{width:44px;height:34px;background:var(--gold)}
.brand-name{font-family:'Ubuntu',sans-serif;font-weight:500;font-size:44px;color:var(--plum);letter-spacing:-0.5px}
.call{right:191px;top:17px;font-family:'Ubuntu',sans-serif;font-size:14px;color:#444;letter-spacing:.3px}
.social{right:192px;top:54px;display:flex;gap:7px}
.social span{width:27px;height:27px;border-radius:50%;background:#e2e2e2;box-shadow:0 1px 2px rgba(0,0,0,.25)}
.social span:first-child{background:#1d9bd6}
.nav{left:196px;top:98px;display:flex;font-family:'Ubuntu',sans-serif;font-size:10px;color:#444;letter-spacing:.2px}
.nav .item{padding:0 17px;border-right:1px solid #aaa;height:12px;line-height:12px;display:block}
.nav .item:first-child{padding-left:4px}
.nav .item:last-child{border-right:none;padding-right:0}
.nav .active{color:var(--plum);font-weight:700;position:relative}
.nav .active::after{content:"";position:absolute;left:0;right:13px;top:20px;height:3px;background:var(--plum)}
.hero{left:0;top:122px;width:1034px;height:332px;background:linear-gradient(120deg,#c9c4c3 0%,#7a6f6e 22%,#d9b7a4 45%,#c89c87 55%,#e7e4e4 75%,#b7b9bf 100%)}
.hero-title{left:0;top:253px;width:1034px;text-align:center;font-family:'Ubuntu',sans-serif;font-style:italic;font-weight:700;font-size:28px;line-height:30px;color:#fff;letter-spacing:-.5px;text-shadow:0 1px 3px rgba(0,0,0,.3)}
.dots{left:777px;top:385px;display:flex;gap:6px}
.dots span{width:9px;height:9px;border-radius:50%;border:2px solid #fff;background:rgba(255,255,255,.4)}
.dots span:first-child{background:var(--plum)}
.service-band{left:0;top:452px;width:1034px;height:4px;background:var(--plum)}
.service-strip{left:0;top:456px;width:1034px;height:50px;background:linear-gradient(#eee,#fff)}
.service{top:425px;width:140px;text-align:center}
.service .disc{width:54px;height:54px;margin:0 auto;border-radius:50%;background:#666;border:3px solid #fff;box-shadow:0 1px 4px rgba(0,0,0,.35);display:flex;align-items:center;justify-content:center}
.service.active .disc{background:var(--plum);box-shadow:0 3px 0 var(--gold),0 1px 4px rgba(0,0,0,.35)}
.service .label{margin-top:11px;font-family:'Ubuntu',sans-serif;font-weight:500;font-size:10.5px;color:#222}
.heading{font-family:'Ubuntu',sans-serif;font-style:italic;font-weight:700;font-size:17px;color:var(--plum);letter-spacing:-.3px;border-bottom:1px solid var(--rule);padding-bottom:4px}
.about{left:198px;top:532px;width:414px}
.about p{font-size:10.4px;line-height:18px;color:#333;margin-top:10px}
.about p+p{margin-top:13px}
.read-more{display:block;text-align:right;margin-top:9px;font-size:10.5px;color:var(--gold);text-decoration:none}
.team{left:642px;top:528px;width:192px;height:192px;border-radius:50%;border:3px solid var(--plum);overflow:hidden;box-shadow:0 10px 10px -6px rgba(0,0,0,.3)}
.team-photo{width:100%;height:128px;background:linear-gradient(#f4f4f4,#c6d2e2 60%,#8e9fb8)}
.team-label{height:64px;background:var(--plum);color:#fff;text-align:center;font-family:'Ubuntu',sans-serif;font-weight:500;font-size:20px;padding-top:10px}
.col-head{top:756px;width:310px}
.box{top:792px;width:310px;height:226px;border:1px solid #ccc;border-radius:2px;background:#fff;padding:3px;box-shadow:0 8px 8px -5px rgba(0,0,0,.25)}
.box-inner{width:100%;height:100%;background:var(--panel)}
.quote{display:flex;height:110px;border-bottom:1px solid #ddd;margin:0 8px}
.quote:last-child{border-bottom:none}
.person{width:92px;text-align:center;padding-top:9px}
.avatar{width:62px;height:62px;margin:0 auto;border-radius:50%;border:3px solid #fff;background:linear-gradient(#c5c9ce,#5d6673);box-shadow:0 1px 3px rgba(0,0,0,.3)}
.person .name{font-family:'Ubuntu',sans-serif;font-weight:500;font-size:12px;color:#222;margin-top:4px}
.person .role{font-size:9px;color:#666}
.quote-text{flex:1;border-left:1px solid #ddd;margin:12px 0 10px 10px;padding:6px 0 0 23px;font-size:9px;line-height:13.5px;color:#333;position:relative}
.quote-text::before{content:"\201C";position:absolute;left:2px;top:-6px;font-family:Georgia,serif;font-size:26px;color:#999}
.news{display:flex;gap:18px;margin:0 14px;height:74px;padding-top:16px;border-bottom:1px solid #ddd}
.news:last-child{border-bottom:none}
.news .date{font-family:'Ubuntu',sans-serif;font-weight:500;font-size:10px;color:var(--plum)}
.news p{font-family:'Ubuntu',sans-serif;font-size:10px;line-height:13.5px;color:#333;margin-top:5px;max-width:200px}
.pager{top:1023px;display:flex;gap:7px}
.pager span{width:14px;height:14px;border-radius:50%;border:1px solid #555;display:flex;align-items:center;justify-content:center}
.site-footer{color:var(--footer-text)}
.footer{left:0;top:1058px;width:1034px;height:120px;background:var(--footer)}
.foot-title{font-family:'Ubuntu',sans-serif;font-weight:400;font-size:13px;color:var(--footer-text)}
.links{left:198px;top:1070px}
.link-cols{display:flex;gap:30px;margin-top:10px}
.link-cols ul{list-style:none;width:55px}
.link-cols li{font-family:'Ubuntu',sans-serif;font-size:8.5px;letter-spacing:.3px;line-height:18px;padding-left:11px;position:relative;color:var(--footer-text);white-space:nowrap}
.link-cols li::before{content:"\203A";position:absolute;left:0;top:-1px;color:var(--gold);font-size:11px}
.vrule{top:1078px;width:1px;height:56px;background:#4a4a4a}
.newsletter{left:430px;top:1070px;width:160px}
.newsletter p{font-size:9.5px;line-height:11px;margin-top:9px;color:var(--footer-text)}
.field{width:114px;height:17px;background:#fff;margin-top:6px;border-radius:2px;font-size:7.5px;color:#999;padding:4px 5px}
.submit{display:inline-block;margin-top:6px;background:var(--plum);color:#fff;border:1px solid #fff;border-radius:2px;font-family:'Ubuntu',sans-serif;font-weight:700;font-size:9px;line-height:11px;padding:3px 7px}
.contact{left:635px;top:1070px;width:210px}
.map{left:635px;top:1099px;width:81px;height:63px;background:linear-gradient(135deg,#e8e6e0,#d4d2cb)}
.contact-list{left:728px;top:1100px;width:125px;list-style:none}
.contact-list li{display:flex;gap:7px;font-size:9px;line-height:11px;margin-bottom:5px;color:var(--footer-text)}
.contact-list svg{flex:none;margin-top:1px}
.copyright{left:0;top:1178px;width:1034px;height:22px;background:var(--plum);color:#fff;text-align:center;font-family:'Ubuntu',sans-serif;font-size:10.5px;line-height:22px}
</style>
</head>
<body>
<div class="abs top-rule"></div>

<header>
  <div class="abs brand"><span class="brand-mark"></span><span class="brand-name">plumbwick</span></div>
  <div class="abs call">CALL US: 020 7946 0182</div>
  <div class="abs social" aria-label="Social links"><span></span><span></span><span></span><span></span></div>
  <nav class="abs nav">
    <span class="item active">HOME</span>
    <span class="item">ABOUT US</span>
    <span class="item">WHAT WE DO</span>
    <span class="item">NEWS BLOG</span>
    <span class="item">ARTICLES</span>
    <span class="item">CLIENTS</span>
    <span class="item">PARTNERS</span>
    <span class="item">CONTACT US</span>
  </nav>
</header>

<section>
  <div class="abs hero" role="img" aria-label="Photo of a business team stacking hands together, seen from below"></div>
  <h1 class="abs hero-title">SERIOUS IT SUPPORT<br>FOR BUSINESS</h1>
  <div class="abs dots"><span></span><span></span><span></span></div>
  <div class="abs service-band"></div>
  <div class="abs service-strip"></div>

  <div class="abs service" style="left:188px">
    <div class="disc"><svg width="26" height="26" viewBox="0 0 26 26"><path d="M18 3a5 5 0 0 0-5 6.5L4 18.5a2 2 0 0 0 3 3l9-9A5 5 0 0 0 23 8l-3 3-3-1-1-3 3-3a5 5 0 0 0-1-1z" fill="#fff"/></svg></div>
    <div class="label">It Support &amp; Management</div>
  </div>
  <div class="abs service" style="left:319px">
    <div class="disc"><svg width="30" height="22" viewBox="0 0 30 22"><path d="M8 19a5 5 0 0 1 0-10 7 7 0 0 1 13-2 5 5 0 0 1 2 12z" fill="none" stroke="#fff" stroke-width="2.5"/></svg></div>
    <div class="label">Cloud Computing</div>
  </div>
  <div class="abs service active" style="left:448px">
    <div class="disc"><svg width="20" height="28" viewBox="0 0 20 28"><path d="M10 1c3 4 7 6 7 11a7 7 0 0 1-14 0c0-3 2-4 3-6 1 2 2 3 3 3 0-3 0-5 1-8z" fill="#fff"/><rect x="5" y="16" width="10" height="11" rx="1" fill="#fff" stroke="#8e0f50"/></svg></div>
    <div class="label">Disaster Recovery</div>
  </div>
  <div class="abs service" style="left:580px">
    <div class="disc"><svg width="22" height="28" viewBox="0 0 22 28"><rect x="6" y="1" width="10" height="18" rx="1" fill="#fff"/><path d="M11 19v5M3 25h16" stroke="#fff" stroke-width="2"/></svg></div>
    <div class="label">Virtualisation</div>
  </div>
  <div class="abs service" style="left:703px">
    <div class="disc"><svg width="28" height="26" viewBox="0 0 28 26"><path d="M14 2 3 24h6l5-10 5 10h6z M8 17h12" fill="none" stroke="#fff" stroke-width="3"/></svg></div>
    <div class="label">CAD Services</div>
  </div>
</section>

<section class="abs about">
  <h2 class="heading">ABOUT US</h2>
  <p>Lorem ipsum dolor sit amet, consectetuer adipiscing elit, sed diam nonummy nibh euismod tincidunt ut laoreet dolore magna aliquam erat volutpat. Ut wisi enim ad minim veniam, quis nostrud exerci tation ullamcorper suscipit lobortis nisl ut aliquip ex ea comsed diam nonummy nibh euismod tincidunt ut laoreet dolore magna aliquam erat volutpat.</p>
  <p>Lorem ipsum dolor sit amet, consectetuer adipiscing elit, sed diam nonummy nibh euismod tincidunt ut laoreet dolore magna aliquam erat volutpat. Ut wisi enim ad minim veniam, quis nostrud....</p>
  <a class="read-more" href="#">READ MORE...</a>
</section>

<div class="abs team">
  <div class="team-photo" role="img" aria-label="Group photo of the support team"></div>
  <div class="team-label">OUR TEAM</div>
</div>

<h2 class="abs heading col-head" style="left:198px">TESTIMONIALS</h2>
<div class="abs box" style="left:198px">
  <div class="box-inner">
    <div class="quote">
      <div class="person"><div class="avatar" role="img" aria-label="Portrait of client"></div><div class="name">Daniel Harrow</div><div class="role">Businessman</div></div>
      <div class="quote-text">Lorem ipsum dolor sit amet, consectetuer adipiscing elit, sed diam nonummy nibh euismod tincidunt ut laoreet dolore magna aliquam erat volutpat. Ut wisi enim ad minim.</div>
    </div>
    <div class="quote">
      <div class="person"><div class="avatar" role="img" aria-label="Portrait of client"></div><div class="name">Daniel Harrow</div><div class="role">Businessman</div></div>
      <div class="quote-text">Lorem ipsum dolor sit amet, consectetuer adipiscing elit, sed diam nonummy nibh euismod tincidunt ut laoreet dolore magna aliquam erat volutpat. Ut wisi enim ad minim.</div>
    </div>
  </div>
</div>
<div class="abs pager" style="left:327px"><span><svg width="8" height="8" viewBox="0 0 8 8"><path d="M7 4H1M3.5 1.5 1 4l2.5 2.5" fill="none" stroke="#444"/></svg></span><span><svg width="8" height="8" viewBox="0 0 8 8"><path d="M1 4h6M4.5 1.5 7 4 4.5 6.5" fill="none" stroke="#444"/></svg></span></div>

<h2 class="abs heading col-head" style="left:534px">LATEST NEWS</h2>
<div class="abs box" style="left:534px">
  <div class="box-inner">
    <div class="news"><svg width="30" height="30" viewBox="0 0 30 30"><rect x="2" y="5" width="26" height="23" rx="2" fill="none" stroke="#666" stroke-width="2.5"/><path d="M8 2v6M22 2v6M2 11h26" stroke="#666" stroke-width="2.5"/><g fill="#666"><rect x="7" y="14" width="4" height="3"/><rect x="13" y="14" width="4" height="3"/><rect x="19" y="14" width="4" height="3"/><rect x="7" y="20" width="4" height="3"/><rect x="13" y="20" width="4" height="3"/><rect x="19" y="20" width="4" height="3"/></g></svg><div><div class="date">12-APR-2014</div><p>Lorem ipsum dolor sit amet, consectetuer adipiscil ng elit, sed diam nonummy nibh...</p></div></div>
    <div class="news"><svg width="30" height="30" viewBox="0 0 30 30"><rect x="2" y="5" width="26" height="23" rx="2" fill="none" stroke="#666" stroke-width="2.5"/><path d="M8 2v6M22 2v6M2 11h26" stroke="#666" stroke-width="2.5"/><g fill="#666"><rect x="7" y="14" width="4" height="3"/><rect x="13" y="14" width="4" height="3"/><rect x="19" y="14" width="4" height="3"/><rect x="7" y="20" width="4" height="3"/><rect x="13" y="20" width="4" height="3"/><rect x="19" y="20" width="4" height="3"/></g></svg><div><div class="date">15-APR-2014</div><p>Lorem ipsum dolor sit amet, consectetuer adipiscil ng elit, sed diam nonummy nibh...</p></div></div>
    <div class="news"><svg width="30" height="30" viewBox="0 0 30 30"><rect x="2" y="5" width="26" height="23" rx="2" fill="none" stroke="#666" stroke-width="2.5"/><path d="M8 2v6M22 2v6M2 11h26" stroke="#666" stroke-width="2.5"/><g fill="#666"><rect x="7" y="14" width="4" height="3"/><rect x="13" y="14" width="4" height="3"/><rect x="19" y="14" width="4" height="3"/><rect x="7" y="20" width="4" height="3"/><rect x="13" y="20" width="4" height="3"/><rect x="19" y="20" width="4" height="3"/></g></svg><div><div class="date">17-APR-2014</div><p>Lorem ipsum dolor sit amet, consectetuer adipiscil ng elit, sed diam nonummy nibh...</p></div></div>
  </div>
</div>
<div class="abs pager" style="left:671px"><span><svg width="8" height="8" viewBox="0 0 8 8"><path d="M7 4H1M3.5 1.5 1 4l2.5 2.5" fill="none" stroke="#444"/></svg></span><span><svg width="8" height="8" viewBox="0 0 8 8"><path d="M1 4h6M4.5 1.5 7 4 4.5 6.5" fill="none" stroke="#444"/></svg></span></div>

<footer class="site-footer">
  <div class="abs footer"></div>
  <div class="abs links">
    <h3 class="foot-title">Quick Links</h3>
    <div class="link-cols">
      <ul><li>HOME</li><li>ABOUT US</li><li>WHAT WE DO</li><li>NEWS BLOG</li></ul>
      <ul><li>ARTICLES</li><li>CLIENTS</li><li>PARTNERS</li><li>CONTACT US</li></ul>
    </div>
  </div>
  <div class="abs vrule" style="left:388px"></div>
  <div class="abs newsletter">
    <h3 class="foot-title">Newsletter Signup</h3>
    <p>Lorem ipsum dolor sit amet,<br>consectetuer adipiscing elit.</p>
    <div class="field">Enter your email address</div>
    <span class="submit">SUBMIT</span>
  </div>
  <div class="abs vrule" style="left:594px"></div>
  <div class="abs contact"><h3 class="foot-title">Contact Info</h3></div>
  <div class="abs map" role="img" aria-label="Street map showing office location"></div>
  <ul class="abs contact-list">
    <li><svg width="9" height="12" viewBox="0 0 9 12"><path d="M4.5 0a4.5 4.5 0 0 0-4.5 4.5C0 8 4.5 12 4.5 12S9 8 9 4.5A4.5 4.5 0 0 0 4.5 0z" fill="#e1b000"/><circle cx="4.5" cy="4.5" r="1.6" fill="#333"/></svg><span>Lorem ipsum dolor sit amet, consectetuer adipiscing elit.</span></li>
    <li><svg width="10" height="10" viewBox="0 0 10 10"><circle cx="5" cy="5" r="4.3" fill="none" stroke="#e1b000" stroke-width="1.2"/><path d="M3.5 2.8l1 1-.6.8a4 4 0 0 0 1.5 1.5l.8-.6 1 1-.7.8C4.5 7 3 5.5 2.7 3.5z" fill="#e1b000"/></svg><span>020 7946 0182</span></li>
    <li><svg width="11" height="8" viewBox="0 0 11 8"><rect width="11" height="8" fill="#e1b000"/><path d="M0 0l5.5 4.5L11 0" fill="none" stroke="#333"/></svg><span>website@plumbwick.net</span></li>
  </ul>
  <div class="abs copyright">© 2014 plumbwick. All Rights Reserved.</div>
</footer>
</body>
</html>
```